Small legal and financial translation company needs Squarespace website, brochure and logo

Hello,
We are Lumarin Services (www.lumarinservices-example.com), a boutique legal and financial translation company. We offer our services mainly to Spanish customers. Our primary line of business is the translation of financial statements, but we translate a wide variety legal and financial texts.
The project we are offering comprises three parts: a redo of the current website, an informational brochure for potential customer and a logo design. These three parts should provide a consistent image. We would develop content soon.
We are looking for a website that would look like a typical law firm website, nothing too fancy. Right now, it is in English, Spanish and French, although the new site need only be in English and Spanish. There must be good toggling between the English and Spanish versions. There would be no need for tie-ins to social media and it would not contain a blog. Basically, a static site. We aren't interesting in driving traffic to the site or SEO, as we will contact nearly all potential customers beforehand. The website must be built in Squarespace to enable a smooth transition. The content would be similar to the current page, we'll be working on the exact content, but a rough draft is attached.
The brochure will be some three pages and would introduce the company to potential customers, using similar images as the website and the logo to be designed.
The only specifications for the logo is, as the website and brochure, it convey a sense of security and trust.
Feel free to ask with any questions as this is the first time we have used this platform.
Thank you!
Updates

I've added a more or less final version for the text in the brochure and updated the brief. Added Wednesday, June 10, 2015

Target Market(s)

Spanish law firms, auditors, accountants, banks, investment firms

Industry/Entity Type

Finance

Logo Text

Lumarin Services

Number of Pages Required

5+ page

Font styles to use
Serif

Requirements
Must have
• The website must be built in Squarespace and have a good option to toggle between English and Spanish versions.
• Brochure must be in both English and Spanish, I'm attaching a rough draft of the information that it will probably have. This should give an idea about what to include and the spacing. I will update it to include the final information.
Nice to have
• Would be nice to have some quality finance- and legal-related images
Should not have
• Vibrant colours

```html
<!DOCTYPE html>
<html lang="en">
<head>
<meta charset="utf-8">
<title>Lumarin Services – Legal translation brochure spread</title>
<link href="https://fonts.googleapis.com/css2?family=Tinos:ital,wght@0,400;0,700;1,700&display=swap" rel="stylesheet">
<style>
  :root {
    --backdrop: #e7e4df;
    --page-dark: #1f1f1f;
    --page-dark-edge: #3a3a3a;
    --ink-light: #f2f2f2;
    --ink-soft: #d4d4d4;
    --accent: #6fc597;
    --band-light: #62c08c;
    --band-dark: #1f6b48;
    --photo-light: #e6e6e6;
    --photo-mid: #a9a9a9;
    --photo-dark: #3c3c3c;
  }
  * { margin: 0; padding: 0; box-sizing: border-box; }
  html, body { width: 1200px; height: 537px; overflow: hidden; }
  body {
    position: relative;
    background: var(--backdrop);
    font-family: "Tinos", "Times New Roman", serif;
  }
  .spread {
    position: absolute;
    left: 48px; top: 72px;
    width: 1112px; height: 393px;
    box-shadow: 0 4px 12px rgba(0,0,0,0.25);
  }
  .page-left {
    position: absolute; left: 0; top: 0;
    width: 557px; height: 383px;
  }
  .photo-hero {
    position: absolute; inset: 0;
    background:
      radial-gradient(ellipse 40% 55% at 62% 60%, var(--photo-dark) 0%, rgba(60,60,60,0.6) 45%, rgba(0,0,0,0) 75%),
      radial-gradient(ellipse 20% 60% at 15% 55%, rgba(40,40,40,0.85) 0%, rgba(0,0,0,0) 70%),
      linear-gradient(90deg, var(--photo-mid) 0%, var(--photo-light) 45%, var(--photo-mid) 100%);
  }
  .brand-mark {
    position: absolute; left: 234px; top: 340px;
    color: var(--ink-light);
    font-size: 14px; font-weight: 400;
    letter-spacing: 0.5px;
  }
  .page-right {
    position: absolute; left: 557px; top: 0;
    width: 555px; height: 383px;
    background: linear-gradient(90deg, #111 0%, var(--page-dark) 10%, var(--page-dark-edge) 55%, var(--page-dark) 100%);
    color: var(--ink-soft);
  }
  .band {
    position: absolute; top: 383px; height: 10px;
  }
  .band-left { left: 0; width: 557px; background: linear-gradient(180deg, #bfe8cf, var(--band-light)); }
  .band-right { left: 557px; width: 555px; background: var(--band-dark); }

  .section-title {
    position: absolute; right: 25px;
    font-size: 22px; font-weight: 700; font-style: italic;
    color: var(--ink-light);
  }
  .section-rule {
    position: absolute; right: 25px; height: 2px;
    background: var(--ink-light);
  }
  .lead {
    position: absolute; left: 263px; width: 275px;
    color: var(--accent);
    font-size: 16px; line-height: 15px;
  }
  .services {
    position: absolute; left: 266px;
    display: grid; grid-template-columns: 108px 160px;
    grid-auto-flow: column; grid-template-rows: repeat(6, 16px);
    list-style: none;
    font-size: 11px; color: var(--ink-soft);
  }
  .services li { position: relative; padding-left: 10px; white-space: nowrap; }
  .services li::before {
    content: ""; position: absolute; left: 0; top: 5px;
    width: 4px; height: 4px; border-radius: 50%;
    background: var(--accent);
  }
  .photo-thumb {
    position: absolute; left: 50px; width: 115px;
    border: 1px solid #555;
  }
  .photo-courtroom {
    top: 218px; height: 76px;
    background: linear-gradient(180deg, #6e6e6e 0%, #3b3b3b 55%, #1c1c1c 100%);
  }
  .photo-team {
    top: 302px; height: 70px;
    background: linear-gradient(180deg, #8a8a8a 0%, #444 50%, #161616 100%);
  }
</style>
</head>
<body>
  <div class="spread">
    <section class="page-left">
      <div class="photo-hero" role="img" aria-label="Black-and-white photo of a bronze Lady Justice statuette with scales in front of a professional writing at a desk"></div>
      <span class="brand-mark">Lumarin Services</span>
    </section>

    <section class="page-right" lang="en">
      <h2 class="section-title" style="top:27px;">Legal translation</h2>
      <div class="section-rule" style="top:51px; width:480px;"></div>
      <p class="lead" style="top:58px;">Legal translation includes but is not limited to:</p>
      <ul class="services" style="top:97px;">
        <li>all manner of deeds</li>
        <li>contracts</li>
        <li>due diligence</li>
        <li>bylaws</li>
        <li>expert reports</li>
        <li>lawsuits</li>
        <li>appeals</li>
        <li>loan agreements</li>
        <li>powers of attorney</li>
        <li>judgments and court orders</li>
        <li>M&amp;A agreements</li>
        <li>LBOs</li>
      </ul>

      <div class="photo-thumb photo-courtroom" role="img" aria-label="Photo of a courtroom hearing"></div>
      <div class="photo-thumb photo-team" role="img" aria-label="Photo of a group of business professionals"></div>

      <h2 class="section-title" lang="es" style="top:206px;">Traducción Jurídica</h2>
      <div class="section-rule" style="top:229px; width:275px;"></div>
      <p class="lead" lang="es" style="top:237px;">Traducción jurídica incluye pero no se limita a:</p>
      <ul class="services" lang="es" style="top:275px;">
        <li>odo tipo de actos</li>
        <li>contratos</li>
        <li>debida diligencia</li>
        <li>estatutos</li>
        <li>informes periciales</li>
        <li>pleitos</li>
        <li>apelaciones</li>
        <li>contratos de préstamo</li>
        <li>poderes</li>
        <li>sentencias y órdenes judiciales;</li>
        <li>Fusiones y acuerdos</li>
        <li>LBO</li>
      </ul>
    </section>

    <div class="band band-left"></div>
    <div class="band band-right"></div>
  </div>
</body>
</html>
```